Thornvale Group needs a business card design

We need a new business card design using the logo recently selected in a logo competition on Pixel Bazaar. Our business is a consultancy specializing in aviation and energy and the winning business card design will promote an image of precision and professionalism with creativity.

Please use the logo with the name on the front of the card and use a complementary font. Make the back white with either the light grey or dark grey logo.

Target Market(s)

Senior finance and legal leaders at aviation and energy companies

Industry/Entity Type

Management Consulting

Contact Information for Business Card

Peter Castrell
President
Thornvale Group

www.thornvalegroup.example

(555) 204-6391
pc@thornvalegroup.example

Requirements
Must have
• Professional font that goes well with the logo font

```html
<!DOCTYPE html>
<html lang="en">
<head>
<meta charset="utf-8">
<title>Thornvale Group – Business Cards</title>
<link rel="stylesheet" href="https://fonts.googleapis.com/css2?family=Open+Sans:wght@400;600;700&display=swap">
<style>
  :root {
    --navy: #12426f;
    --stripe: #6d6e70;
    --paper: #ffffff;
    --backdrop: #e9e7e3;
    --light-text: #ffffff;
  }
  * { box-sizing: border-box; margin: 0; padding: 0; }
  html, body {
    width: 1200px;
    height: 900px;
    overflow: hidden;
  }
  body {
    background: var(--backdrop);
    font-family: "Open Sans", Arial, sans-serif;
    position: relative;
  }
  .card {
    position: absolute;
    width: 540px;
    height: 309px;
    background: var(--paper);
    box-shadow: 0 10px 24px rgba(0,0,0,0.18);
    overflow: hidden;
  }
  .card--services { left: 110px; top: 110px; }
  .card--contact  { left: 560px; top: 470px; }

  .card__top {
    height: 168px;
    display: flex;
    align-items: center;
    justify-content: center;
  }
  .card__stripe {
    height: 7px;
    background: var(--stripe);
  }
  .card__band {
    height: 134px;
    background: var(--navy);
    color: var(--light-text);
    display: flex;
    align-items: center;
    justify-content: center;
  }

  .brand-name {
    font-weight: 400;
    color: var(--navy);
    font-size: 38px;
    letter-spacing: 3px;
    text-transform: uppercase;
    text-align: center;
    line-height: 1.15;
  }
  .brand-name span { display: block; font-size: 20px; letter-spacing: 14px; padding-left: 14px; }

  /* services side */
  .card--services .card__band { gap: 30px; padding-left: 60px; }
  .tagline {
    font-weight: 700;
    font-size: 17px;
    line-height: 1.3;
    text-align: right;
    text-transform: uppercase;
  }
  .tagline span {
    display: block;
    border-bottom: 1.5px solid var(--light-text);
    padding-bottom: 1px;
  }
  .sectors { list-style: none; font-size: 14px; font-weight: 600; margin-top: -18px; }
  .sectors li { display: flex; align-items: center; gap: 8px; line-height: 1.5; }
  .sectors li:nth-child(2) { padding-left: 6px; }
  .sectors li:nth-child(3) { padding-left: 12px; }
  .sectors svg { width: 11px; height: 9px; fill: var(--light-text); }

  /* contact side */
  .card--contact .card__band { justify-content: space-between; padding: 0 40px 0 60px; }
  .person { text-align: right; margin-top: 28px; }
  .person__name { font-weight: 700; font-size: 21px; }
  .person__title { font-size: 15px; }
  .contact { list-style: none; font-size: 13px; margin-top: -22px; }
  .contact li { display: flex; align-items: center; gap: 9px; line-height: 1.7; }
  .contact svg { width: 11px; height: 11px; fill: var(--light-text); }
</style>
</head>
<body>

  <section class="card card--services" aria-label="Business card, services side">
    <div class="card__top">
      <p class="brand-name">Thornvale<span>Group</span></p>
    </div>
    <div class="card__stripe"></div>
    <div class="card__band">
      <p class="tagline"><span>Finance and</span><span>Strategy</span><span>Consulting</span></p>
      <ul class="sectors">
        <li><svg viewBox="0 0 11 9"><path d="M0 4.5 11 0 6 4.5 11 9z"/></svg>Aviation</li>
        <li><svg viewBox="0 0 11 9"><path d="M0 4.5 11 0 6 4.5 11 9z"/></svg>Manufacturing</li>
        <li><svg viewBox="0 0 11 9"><path d="M0 4.5 11 0 6 4.5 11 9z"/></svg>Energy</li>
      </ul>
    </div>
  </section>

  <section class="card card--contact" aria-label="Business card, contact side">
    <div class="card__top">
      <p class="brand-name">Thornvale<span>Group</span></p>
    </div>
    <div class="card__stripe"></div>
    <div class="card__band">
      <div class="person">
        <p class="person__name">Peter Castrell</p>
        <p class="person__title">President</p>
      </div>
      <ul class="contact">
        <li><svg viewBox="0 0 24 24"><path d="M6.6 10.8a15 15 0 0 0 6.6 6.6l2.2-2.2c.3-.3.7-.4 1-.2 1.1.4 2.3.6 3.6.6.6 0 1 .4 1 1V20c0 .6-.4 1-1 1A17 17 0 0 1 3 4c0-.6.4-1 1-1h3.5c.6 0 1 .4 1 1 0 1.3.2 2.5.6 3.6.1.3 0 .7-.2 1z"/></svg>(555) 204-6391</li>
        <li><svg viewBox="0 0 24 24"><path d="M2 5h20v14H2zm2 2v.5l8 5 8-5V7zm0 3v7h16v-7l-8 5z"/></svg>pc@thornvalegroup.example</li>
      </ul>
    </div>
  </section>

</body>
</html>
```